Professional Package for CPA Firm

We would like a stationery design for our new CPA Firm based in Atlanta, GA called 'Vale 8'. We work with investors to help grow investments, tax free. We would like the design to have a professional/minimal look with a 'wow' factor. We need 9.5″ x 4.125″, 9x12, and 10x13 mailing envelopes, business cards, and a letterhead. We have a logo that is already complete. For the letterhead, we would like to have space to put credentials at the bottom of the page

Industry/Entity Type

CPA, Accounting

```html
<!DOCTYPE html>
<html lang="en">
<head>
<meta charset="utf-8">
<title>Vale 8 — Business Card</title>
<link href="https://fonts.googleapis.com/css2?family=Lato:wght@400;700&display=swap" rel="stylesheet">
<style>
  :root {
    --navy: #0b2238;
    --navy-deep: #061827;
    --blue-light: #1f5f86;
    --teal: #1aa3b5;
    --teal-soft: #5fc3cf;
    --white: #ffffff;
    --paper: #f4f5f6;
    --stage: #e4e6e9;
    --ink: #102a40;
  }
  * { box-sizing: border-box; margin: 0; padding: 0; }
  html, body {
    width: 1200px; height: 874px; overflow: hidden;
    background: var(--stage);
    font-family: "Lato", Arial, sans-serif;
  }
  .sheet {
    width: 1200px; height: 874px;
    display: flex; flex-direction: column;
    align-items: center; justify-content: center; gap: 26px;
  }
  .card {
    position: relative;
    width: 700px; height: 400px;
    overflow: hidden;
    box-shadow: 0 6px 18px rgba(0,0,0,.18);
  }

  /* Back side */
  .card-back { background: var(--navy); }
  .card-back .texture {
    position: absolute; inset: 0;
    background: linear-gradient(115deg, var(--blue-light) 0%, #123a58 35%, var(--navy) 65%, var(--navy-deep) 100%);
  }
  .card-back .brand-mini {
    position: absolute; right: 40px; bottom: 30px;
    color: var(--white); font-weight: 700; font-size: 22px; letter-spacing: 1px;
  }

  /* Front side */
  .card-front { background: linear-gradient(160deg, var(--white) 40%, #e9eaec 100%); }
  .brand {
    position: absolute; left: 64px; top: 80px;
  }
  .brand-name {
    display: flex; align-items: center; gap: 14px;
    color: var(--ink); font-weight: 700; font-size: 52px; letter-spacing: 3px;
    text-transform: uppercase; line-height: 1;
  }
  .brand-dot {
    width: 22px; height: 22px; border-radius: 50%; background: var(--teal);
  }
  .brand-tag {
    margin-top: 10px; color: var(--ink); font-size: 15px; letter-spacing: 2px;
  }
  .panel { position: absolute; inset: 0; }
  .details {
    position: absolute; right: 62px; bottom: 34px;
    text-align: right; color: var(--white);
  }
  .person-name {
    color: var(--teal); font-weight: 700; font-size: 24px; letter-spacing: 1px;
    text-transform: uppercase;
  }
  .person-title { color: var(--teal); font-size: 16px; margin-bottom: 10px; }
  .address { font-size: 16px; line-height: 1.25; margin-bottom: 12px; }
  .contact-list { list-style: none; font-size: 16px; line-height: 1.4; }
  .contact-list li { display: flex; justify-content: flex-end; align-items: center; gap: 8px; }
  .contact-list svg { width: 13px; height: 13px; flex: none; }
</style>
</head>
<body>
<main class="sheet">

  <section class="card card-back" aria-label="Card back">
    <div class="texture" role="img" aria-label="Tonal navy-to-blue repeating pattern"></div>
    <span class="brand-mini">Vale 8</span>
  </section>

  <section class="card card-front" aria-label="Card front">
    <div class="brand">
      <div class="brand-name"><span class="brand-dot"></span>Vale 8</div>
      <div class="brand-tag">CPAs and Tax Advisors</div>
    </div>

    <svg class="panel" viewBox="0 0 700 400" aria-hidden="true">
      <path d="M700 128 L530 128 Q488 128 464 160 L330 400 L700 400 Z" fill="#1aa3b5"/>
      <path d="M700 136 L528 136 Q490 136 468 166 L340 400 L700 400 Z" fill="#0b2238"/>
    </svg>

    <div class="details">
      <div class="person-name">Daniel Hart</div>
      <div class="person-title">President</div>
      <div class="address">4210 Birchwood Lane<br>Atlanta, Georgia 30308</div>
      <ul class="contact-list">
        <li>555-204-3187
          <svg viewBox="0 0 16 16"><path d="M3 1h3l1.5 4-2 1.3a9 9 0 0 0 4.2 4.2L11 8.5 15 10v3a2 2 0 0 1-2 2A12 12 0 0 1 1 3a2 2 0 0 1 2-2z" fill="#1aa3b5"/></svg>
        </li>
        <li>555-761-4920
          <svg viewBox="0 0 16 16"><rect x="4" y="1" width="8" height="14" rx="1.5" fill="none" stroke="#1aa3b5" stroke-width="1.6"/><circle cx="8" cy="12.5" r="1" fill="#1aa3b5"/></svg>
        </li>
        <li>info@vale8.com
          <svg viewBox="0 0 16 16"><rect x="1" y="3" width="14" height="10" rx="1" fill="#1aa3b5"/><path d="M1.5 3.5 8 9l6.5-5.5" fill="none" stroke="#0b2238" stroke-width="1.3"/></svg>
        </li>
        <li>www.vale8.com
          <svg viewBox="0 0 16 16"><circle cx="8" cy="8" r="6.5" fill="none" stroke="#1aa3b5" stroke-width="1.6"/><path d="M1.5 8h13M8 1.5c-3 3.5-3 9.5 0 13M8 1.5c3 3.5 3 9.5 0 13" fill="none" stroke="#1aa3b5" stroke-width="1.2"/></svg>
        </li>
      </ul>
    </div>
  </section>

</main>
</body>
</html>
```